Promotional business a5 Notepad design

I am looking for a custom a5 notepad design as a promotional item to give away to customers etc.
Attached will be a desk planner we had designed feel free to use as a reference.
We want the notepad to have lines running horizontal not squares like the desk planner example.

Industry/Entity Type

Hydraulic / industrial

Colors

Designer to choose colors to be used in the design.

```html
<!DOCTYPE html>
<html lang="en">
<head>
<meta charset="utf-8">
<title>Keystone Hose &amp; Fittings – A5 Notepad</title>
<link rel="stylesheet" href="https://fonts.googleapis.com/css2?family=Oswald:wght@400;500&family=Archivo:wdth,wght@125,700&display=swap">
<style>
  :root {
    --brand-blue: #1a30c2;
    --band-black: #000000;
    --paper: #ffffff;
    --rule: #1a1a1a;
    --on-dark: #ffffff;
  }
  * { margin: 0; padding: 0; box-sizing: border-box; }
  html, body {
    width: 973px;
    height: 1200px;
    overflow: hidden;
    background: var(--paper);
  }
  .notepad-page {
    position: relative;
    width: 973px;
    height: 1200px;
    background: var(--paper);
  }
  .header-band-dark {
    position: absolute;
    left: 0; top: 88px;
    width: 444px; height: 45px;
    background: var(--band-black);
  }
  .header-band-blue {
    position: absolute;
    left: 448px; top: 88px;
    right: 0; height: 45px;
    background: var(--brand-blue);
  }
  .brand {
    position: absolute;
    left: 80px; top: 72px;
    width: 356px;
    height: 77px;
    display: flex;
    align-items: center;
    gap: 12px;
    overflow: hidden;
  }
  .brand-dot {
    width: 74px; height: 74px;
    border-radius: 50%;
    background: var(--brand-blue);
    border: 4px solid var(--paper);
    flex: none;
  }
  .brand-name {
    font-family: "Oswald", sans-serif;
    font-weight: 500;
    font-size: 21px;
    letter-spacing: 1px;
    color: var(--on-dark);
    text-transform: uppercase;
    white-space: nowrap;
  }
  .contact {
    position: absolute;
    top: 93px;
    font-family: "Oswald", sans-serif;
    font-style: normal;
    font-weight: 400;
    font-size: 15px;
    line-height: 17px;
    color: var(--on-dark);
    white-space: nowrap;
  }
  .contact-address { left: 507px; }
  .contact-reach { left: 732px; top: 96px; }
  .writing-rule {
    position: absolute;
    left: 81px;
    width: 814px;
    height: 2px;
    background: var(--rule);
  }
  .website {
    position: absolute;
    left: 0; right: 0;
    top: 1128px;
    text-align: center;
    font-family: "Archivo", sans-serif;
    font-stretch: 125%;
    font-weight: 700;
    font-size: 15px;
    letter-spacing: 1px;
    color: var(--brand-blue);
  }
</style>
</head>
<body>
  <main class="notepad-page">
    <div class="header-band-dark"></div>
    <div class="header-band-blue"></div>

    <div class="brand">
      <span class="brand-dot"></span>
      <span class="brand-name">Keystone Hose &amp; Fittings</span>
    </div>

    <address class="contact contact-address">
      2140 Harbor Ridge Road<br>Fairbanks, Alaska 99701
    </address>
    <address class="contact contact-reach">
      P. 555-014-2290<br>info@keystonehose.com
    </address>

    <div class="writing-rule" style="top:222px"></div>
    <div class="writing-rule" style="top:285px"></div>
    <div class="writing-rule" style="top:348px"></div>
    <div class="writing-rule" style="top:411px"></div>
    <div class="writing-rule" style="top:474px"></div>
    <div class="writing-rule" style="top:537px"></div>
    <div class="writing-rule" style="top:600px"></div>
    <div class="writing-rule" style="top:663px"></div>
    <div class="writing-rule" style="top:726px"></div>
    <div class="writing-rule" style="top:789px"></div>
    <div class="writing-rule" style="top:852px"></div>
    <div class="writing-rule" style="top:915px"></div>
    <div class="writing-rule" style="top:978px"></div>
    <div class="writing-rule" style="top:1040px"></div>

    <footer class="website">WWW.KEYSTONEHOSE.COM</footer>
  </main>
</body>
</html>
```